Business Card for Industrial Distributor

We need a business card design for an industrial distributor. We sell machine parts for the manufacturing and oil industry. We would like the cards to look clean and modern but with a touch of industry.

Our colors are blue/white.

Please feel free to visit our website www.korvelpartsco.com

Target Market(s)

mexican manufacturers in the automobile/aerospace industry

Industry/Entity Type

Industrial

Colors
ffffff
0555a3

```html
<!DOCTYPE html>
<html lang="en">
<head>
<meta charset="utf-8">
<title>Korvel — Business Card</title>
<link rel="stylesheet" href="https://fonts.googleapis.com/css2?family=Ubuntu:wght@400;700&display=swap">
<style>
  :root {
    --brand-blue: #2a44b8;
    --brand-blue-deep: #2238a6;
    --brand-blue-light: #3a55c8;
    --card-white: #ffffff;
    --card-grey: #c9c9c9;
    --text-grey: #9a9a9a;
    --page-bg: #ecebe8;
  }
  html, body {
    margin: 0;
    padding: 0;
    width: 1200px;
    height: 780px;
    overflow: hidden;
    background: var(--page-bg);
    font-family: "Ubuntu", Arial, sans-serif;
  }
  .stage {
    position: relative;
    width: 1200px;
    height: 780px;
  }
  .card {
    position: absolute;
    width: 540px;
    height: 310px;
    border-radius: 3px;
    overflow: hidden;
    box-shadow: 0 6px 18px rgba(0,0,0,0.18);
  }
  .card-front {
    left: 50px;
    top: 150px;
    background: var(--card-white);
  }
  .card-back {
    left: 610px;
    top: 320px;
    background: linear-gradient(135deg, var(--brand-blue-light), var(--brand-blue-deep));
  }
  .front-sweep {
    position: absolute;
    inset: 0;
  }
  .brand {
    position: absolute;
    left: 34px;
    top: 70px;
    display: flex;
    align-items: center;
    gap: 16px;
  }
  .brand-dot {
    width: 66px;
    height: 66px;
    border-radius: 50%;
    background: var(--brand-blue);
  }
  .brand-name {
    font-weight: 700;
    font-size: 84px;
    letter-spacing: -1px;
    color: var(--brand-blue);
    line-height: 1;
  }
  .person {
    position: absolute;
    left: 38px;
    top: 186px;
  }
  .person-name {
    font-weight: 700;
    font-size: 17px;
    color: var(--brand-blue);
    letter-spacing: 0.5px;
  }
  .person-title {
    font-size: 14px;
    color: var(--text-grey);
    margin-top: 2px;
  }
  .contacts {
    position: absolute;
    left: 38px;
    top: 232px;
    list-style: none;
    margin: 0;
    padding: 0;
  }
  .contacts li {
    display: flex;
    align-items: center;
    gap: 8px;
    font-size: 12.5px;
    color: var(--text-grey);
    height: 17px;
  }
  .contact-icon {
    width: 13px;
    height: 13px;
    background: var(--brand-blue);
    display: block;
  }
  .back-name {
    position: absolute;
    left: 0;
    right: 0;
    top: 88px;
    text-align: center;
    font-weight: 700;
    font-size: 96px;
    letter-spacing: -1px;
    color: var(--card-white);
    line-height: 1;
  }
  .industries {
    position: absolute;
    left: 30px;
    right: 30px;
    bottom: 30px;
    color: var(--card-white);
    font-size: 14.5px;
    line-height: 1.35;
    text-align: center;
  }
  .industries p { margin: 0; }
</style>
</head>
<body>
<main class="stage">

  <section class="card card-front" aria-label="Business card front">
    <svg class="front-sweep" width="540" height="310" viewBox="0 0 540 310" aria-hidden="true">
      <defs>
        <linearGradient id="sweepGrey" x1="0" y1="0" x2="1" y2="1">
          <stop offset="0" stop-color="#e3e3e3"/>
          <stop offset="1" stop-color="#bdbdbd"/>
        </linearGradient>
        <linearGradient id="sweepBlue" x1="0" y1="0" x2="1" y2="1">
          <stop offset="0" stop-color="#3a55c8"/>
          <stop offset="1" stop-color="#2238a6"/>
        </linearGradient>
      </defs>
      <path d="M290 0 L380 0 C480 60 535 170 525 310 L478 310 C492 180 430 70 290 0 Z" fill="url(#sweepGrey)"/>
      <path d="M340 0 L540 0 L540 310 L525 310 C535 170 470 50 340 0 Z" fill="url(#sweepBlue)"/>
    </svg>

    <div class="brand">
      <span class="brand-dot" aria-hidden="true"></span>
      <span class="brand-name">Korvel</span>
    </div>

    <div class="person">
      <div class="person-name">DANIEL REYES</div>
      <div class="person-title">Manager</div>
    </div>

    <ul class="contacts">
      <li>
        <svg class="contact-icon" viewBox="0 0 13 13" aria-hidden="true"><rect width="13" height="13" fill="#2a44b8"/><path d="M3.5 3 L5.2 3 L5.8 5 L4.9 5.7 C5.4 6.8 6.2 7.6 7.3 8.1 L8 7.2 L10 7.8 L10 9.5 C6.5 9.8 3.2 6.5 3.5 3 Z" fill="#fff"/></svg>
        (555) 210 - 4400
      </li>
      <li>
        <svg class="contact-icon" viewBox="0 0 13 13" aria-hidden="true"><rect width="13" height="13" fill="#2a44b8"/><rect x="3" y="5" width="7" height="4" fill="#fff"/><rect x="4.5" y="2.8" width="4" height="2" fill="#fff"/><rect x="4.5" y="9" width="4" height="1.5" fill="#fff"/></svg>
        (555) 210 - 4413
      </li>
      <li>
        <svg class="contact-icon" viewBox="0 0 13 13" aria-hidden="true"><rect width="13" height="13" fill="#2a44b8"/><rect x="2.5" y="3.5" width="8" height="6" fill="none" stroke="#fff" stroke-width="1"/><path d="M2.5 3.5 L6.5 7 L10.5 3.5" fill="none" stroke="#fff" stroke-width="1"/></svg>
        sales@korvelpartsco.com
      </li>
      <li>
        <svg class="contact-icon" viewBox="0 0 13 13" aria-hidden="true"><rect width="13" height="13" fill="#2a44b8"/><circle cx="6.5" cy="6.5" r="4" fill="none" stroke="#fff" stroke-width="1"/><path d="M2.5 6.5 H10.5 M6.5 2.5 C4.5 5 4.5 8 6.5 10.5 M6.5 2.5 C8.5 5 8.5 8 6.5 10.5" fill="none" stroke="#fff" stroke-width="0.8"/></svg>
        www.korvelpartsco.com
      </li>
    </ul>
  </section>

  <section class="card card-back" aria-label="Business card back">
    <div class="back-name">Korvel</div>
    <div class="industries">
      <p>Steel Mills | Petrochemical | Wood and Paper | Oil Gas Chemical</p>
      <p>Plastic and Rubber | Food and Beverages | Automotive | Utility</p>
    </div>
  </section>

</main>
</body>
</html>
```